needing web design for aerial and satellite installation comapny

We need our website designing, it needs to be professional and look creative,
We are a aerial and satellite company called Corvid Mend & Reach ()
I like this site design also some of the following maybe:

https://www.skylorn.co.uk/

http://brimwell.co.uk/

http://quillon4guard.co.uk/portfolio/kmt-brimwell/

The design will require coding once the design is complete, i haven't paid for this yet as i want to be sure the design is good before i commit.

The template needs to look professional and look like one of the leading companies.
The site will consist of all the features this site has https://www.skylorn.co.uk/

I like a modern design with the latest technology.

Target Market(s)

tv aerial satellite installation

Industry/Entity Type

Satellite Tv

Number of Pages Required

3 page

Font styles to use
Sans Serif

Colors

Designer to choose colors to be used in the design.

Requirements
Must have
• eb Contest Brief We need our website designing, it needs to be professional and look creative,
• We are a aerial and satellite company called Corvid Mend Reach ()
• I like this site design also some of the following maybe:
• https://www.skylorn.co.uk/
• http://brimwell.co.uk/
• http://quillon4guard.co.uk/portfolio/kmt-brimwell/
• The design will require coding once the design is complete, i haven't paid for this yet as i want to be sure the design is good before i commit.
• The template needs to look professional and look like one of the leading companies.
• The site will consist of all the features this site has https://www.skylorn.co.uk/
• I like a modern design with the latest technology.
Nice to have
• http://brimwell.co.uk/
Should not have
• poor design

```html
<!DOCTYPE html>
<html lang="en">
<head>
<meta charset="utf-8">
<title>Corvid Mend &amp; Reach – Aerial and Satellite Installation</title>
<link rel="stylesheet" href="https://fonts.googleapis.com/css2?family=Roboto:ital,wght@0,400;0,500;0,700;1,400;1,700&display=swap">
<style>
:root{
  --orange:#f0614a;
  --orange-dark:#e2503a;
  --navy:#1b3a7a;
  --navy-deep:#132c60;
  --ink:#222;
  --dark:#1f2330;
  --footer:#222326;
  --footer-line:#3a3b3f;
  --grey-text:#666;
  --light:#f2f2f2;
  --white:#fff;
}
*{box-sizing:border-box;margin:0;padding:0}
html,body{width:1200px;height:3579px;overflow:hidden}
body{font-family:"Roboto",Arial,sans-serif;color:var(--ink);background:var(--white);position:relative}
section,header,footer{position:absolute;left:0;width:1200px}

/* header */
.site-header{top:0;height:131px;background:var(--white)}
.topbar{position:absolute;right:0;top:0;width:800px;height:30px;background:var(--navy);border-bottom-left-radius:30px;display:flex;align-items:center;gap:26px;padding-left:60px;color:var(--white);font-size:13px}
.topbar .pill{border:1px solid var(--white);border-radius:12px;padding:2px 22px;font-size:12px}
.topbar .pill.login{margin-left:22px}
.topbar svg{vertical-align:-2px;margin-right:6px}
.brand{position:absolute;left:96px;top:14px;width:250px;text-align:center}
.brand .mark{width:60px;height:46px;margin:0 auto 10px;background:var(--ink)}
.brand .name{font-size:15px;font-weight:500;letter-spacing:6px;color:var(--ink)}
.main-nav{position:absolute;right:96px;top:76px;display:flex;gap:30px;font-size:16px;font-weight:500;color:var(--ink);text-transform:uppercase}

/* hero */
.hero{top:131px;height:537px}
.hero .photo{position:absolute;inset:0;background:linear-gradient(100deg,#8a8f8a 0%,#b7b9b3 35%,#6f7a6a 60%,#3e4a36 100%)}
.hero h1{position:absolute;left:98px;top:138px;font-size:48px;line-height:52px;font-weight:700;color:var(--white);text-transform:uppercase}
.btn{display:inline-block;background:var(--orange);color:var(--white);font-size:14px;text-transform:uppercase;padding:10px 16px;border-radius:3px}
.hero .btn{position:absolute;left:98px;top:310px}
.dots{position:absolute;left:100px;top:371px;display:flex;gap:6px}
.dots span{width:12px;height:12px;border-radius:50%;border:2px solid #ddd}
.dots span.on{background:var(--white);border-color:var(--white)}

/* section titles */
.section-title{font-size:32px;font-weight:500;text-align:center;text-transform:uppercase;letter-spacing:1px}

/* services */
.services{top:668px;height:525px}
.services .section-title{margin-top:57px}
.service-list{position:absolute;top:143px;left:100px;display:flex;gap:19px}
.service-card{width:235px;height:306px;position:relative;background:var(--navy);color:var(--white);text-align:center;overflow:hidden}
.service-card .top{position:absolute;left:0;top:0;width:100%;height:170px;background:var(--orange)}
.service-card .wave{position:absolute;left:0;top:140px;width:100%;height:50px}
.service-card .icon{position:absolute;left:0;right:0;top:26px;margin:auto}
.service-card h3{position:absolute;top:188px;left:0;right:0;font-size:16px;font-weight:500;text-transform:uppercase}
.service-card p{position:absolute;top:218px;left:22px;right:22px;font-size:12px;line-height:17px;color:#dfe4ef}

/* how it works */
.how{top:1193px;height:525px;color:var(--white)}
.how .bg{position:absolute;inset:0;background:linear-gradient(180deg,#1a2236 0%,#27324a 55%,#3a3a3c 100%)}
.how .section-title{position:relative;margin-top:92px;font-size:32px}
.how .intro{position:relative;width:930px;margin:22px auto 0;font-size:13px;line-height:26px;text-align:center;color:#dde}
.steps{position:absolute;top:283px;left:0;width:1200px;height:150px}
.steps .track{position:absolute;left:217px;top:52px}
.step{position:absolute;top:0;width:220px;margin-left:-110px;text-align:center}
.step .circle{width:104px;height:104px;margin:0 auto;border-radius:50%;background:var(--orange);border:5px solid #2b3348;box-shadow:0 0 0 2px var(--orange);display:flex;align-items:center;justify-content:center}
.step h4{margin-top:18px;font-size:18px;font-weight:500}

/* need a repair */
.repair{top:1718px;height:532px}
.repair .section-title{margin-top:82px}
.repair-cards{position:absolute;top:162px;left:95px;width:1010px;height:264px}
.repair-card{position:absolute;top:0;height:264px;text-align:center;padding-top:62px}
.repair-card.info{background:linear-gradient(160deg,#ececec,#d8d8d8)}
.repair-card.info .veil{position:absolute;inset:0;background:rgba(255,255,255,.55)}
.repair-card>*{position:relative}
.repair-card h3{font-size:24px;font-weight:500;color:#333}
.repair-card p{width:250px;margin:14px auto 0;font-size:12px;line-height:17px;color:#555}
.repair-card .btn-navy{display:inline-block;margin-top:24px;background:var(--navy);color:var(--white);font-size:13px;font-weight:700;padding:7px 16px;text-transform:uppercase}
.repair-card.quick{background:var(--orange);padding-top:30px}
.repair-card.quick h3{color:var(--white)}
.repair-card.quick p{color:#ffe6e0;margin-top:30px}
.repair-card.quick .field{width:278px;height:40px;margin:22px auto 0;background:var(--white);font-size:11px;color:#888;text-align:left;padding:12px 14px}
.repair-card.quick .btn-navy{margin-top:24px;padding:8px 30px}

/* news */
.news{top:2250px;height:489px;background:linear-gradient(180deg,var(--navy) 0%,var(--navy-deep) 100%);color:var(--white)}
.news .section-title{margin-top:56px}
.news-list{position:absolute;top:131px;left:95px;display:flex;gap:29px}
.news-item{width:317px;position:relative}
.news-item .thumb{height:196px}
.news-item .date{position:absolute;left:0;top:212px;width:52px;height:52px;border-radius:50%;background:var(--orange);font-size:9px;line-height:12px;text-align:center;padding-top:14px;font-weight:500}
.news-item h3{margin:14px 0 0 68px;font-size:14px;font-weight:500}
.news-item p{margin:10px 0 0 68px;font-size:11px;line-height:16px;color:#d5dbea}

/* testimonial */
.testimonial{top:2739px;height:315px;background:linear-gradient(90deg,#1c1c1e 0%,#2a2a2c 50%,#1c1c1e 100%);color:var(--white);text-align:center}
.testimonial .corner{position:absolute;width:62px;height:62px;border-color:var(--white);border-style:solid}
.testimonial .corner.tl{left:193px;top:98px;border-width:3px 0 0 3px}
.testimonial .corner.br{right:193px;top:202px;border-width:0 3px 3px 0}
.testimonial .quote-mark{margin-top:42px;font-size:72px;line-height:60px;font-weight:700}
.testimonial blockquote{width:800px;margin:18px auto 0;font-size:13px;line-height:26px;font-style:italic}
.testimonial cite{display:block;margin-top:18px;font-size:15px;font-weight:700;font-style:italic}
.slider-bar{position:absolute;left:590px;top:258px;display:flex;gap:6px}
.slider-bar span{width:24px;height:3px;background:#666}
.slider-bar span.on{background:var(--white)}

/* partners */
.partners{top:3054px;height:120px;background:var(--light);display:flex;align-items:center;justify-content:space-between;padding:0 137px}
.partners span{font-size:26px;font-weight:700;color:#9a9a9a;letter-spacing:1px}

/* footer */
.site-footer{top:3174px;height:405px;background:var(--footer);color:#ccc}
.footer-col{position:absolute;top:62px}
.footer-col h4{font-size:18px;font-weight:500;color:var(--white);text-transform:uppercase;margin-bottom:26px}
.quick-links{left:95px}
.quick-links li{list-style:none;font-size:12px;line-height:21px}
.quick-links li::before{content:"›";margin-right:14px}
.contact{left:286px;width:300px}
.contact .row{display:flex;gap:12px;font-size:12px;line-height:18px;margin-bottom:14px}
.contact .row svg{flex:none;margin-top:2px}
.quote{left:632px;width:472px}
.quote p{font-size:12px;line-height:17px;margin-bottom:22px}
.quote .grid{display:grid;grid-template-columns:1fr 1fr;gap:12px 16px}
.quote .input{height:44px;border:1px solid #aaa;font-size:11px;padding:14px;color:#ddd}
.quote .submit{height:44px;background:#c8282a;color:var(--white);font-size:13px;font-weight:700;text-align:center;padding-top:14px;text-transform:uppercase}
.footer-bottom{position:absolute;left:0;top:298px;width:1200px;border-top:1px solid var(--footer-line);text-align:center}
.socials{display:flex;justify-content:center;gap:8px;margin-top:24px}
.socials span{width:24px;height:24px;border-radius:50%;border:1px solid #ccc}
.copyright{margin-top:16px;font-size:12px;color:#ccc}
</style>
</head>
<body>

<header class="site-header">
  <div class="topbar">
    <span><svg width="12" height="12" viewBox="0 0 24 24" fill="#fff"><path d="M6.6 10.8a15 15 0 0 0 6.6 6.6l2.2-2.2c.3-.3.7-.4 1-.2 1.1.4 2.3.6 3.6.6.6 0 1 .4 1 1V20c0 .6-.4 1-1 1A17 17 0 0 1 3 4c0-.6.4-1 1-1h3.5c.6 0 1 .4 1 1 0 1.3.2 2.5.6 3.6.1.3 0 .7-.2 1z"/></svg>555.014.2290</span>
    <span><svg width="13" height="11" viewBox="0 0 24 20" fill="#fff"><path d="M2 0h20a2 2 0 0 1 2 2v16a2 2 0 0 1-2 2H2a2 2 0 0 1-2-2V2a2 2 0 0 1 2-2zm10 9 10-6V2L12 8 2 2v1z"/></svg>Email: hello@corvidmendreach.example</span>
    <span class="pill login">Login</span>
    <span class="pill">Get a Quote</span>
  </div>
  <div class="brand">
    <div class="mark"></div>
    <div class="name">CORVID MEND &amp; REACH</div>
  </div>
  <nav class="main-nav">
    <span>Home</span><span>What We Do</span><span>Services</span><span>Solutions</span><span>Blog</span><span>Contact Us</span>
  </nav>
</header>

<section class="hero">
  <div class="photo" role="img" aria-label="Technician in blue overalls holding a satellite dish beside a house wall"></div>
  <h1>Aerial and<br>Satellite<br>Installation</h1>
  <span class="btn">Read More</span>
  <div class="dots"><span class="on"></span><span></span><span></span></div>
</section>

<section class="services">
  <h2 class="section-title">Our Services</h2>
  <div class="service-list">
    <article class="service-card">
      <div class="top"></div>
      <svg class="wave" viewBox="0 0 235 50" preserveAspectRatio="none"><path d="M0 30 Q60 0 118 22 T235 10 V50 H0Z" fill="#fff"/><path d="M0 36 Q60 8 118 28 T235 16 V50 H0Z" fill="var(--navy)"/></svg>
      <svg class="icon" width="90" height="90" viewBox="0 0 90 90" fill="none" stroke="#fff" stroke-width="4"><path d="M20 30 A32 32 0 0 0 60 70 Z" fill="#fff"/><line x1="40" y1="50" x2="60" y2="30"/><path d="M66 18a12 12 0 0 1 8 8M68 10a20 20 0 0 1 14 14"/><path d="M34 66 L26 84 H58 L50 66"/></svg>
      <h3>TV Aerial Services</h3>
      <p>Sed ut perspiciatis unde omnis iste natus error sit voluptatem santium doloremque laudantium</p>
    </article>
    <article class="service-card">
      <div class="top"></div>
      <svg class="wave" viewBox="0 0 235 50" preserveAspectRatio="none"><path d="M0 30 Q60 0 118 22 T235 10 V50 H0Z" fill="#fff"/><path d="M0 36 Q60 8 118 28 T235 16 V50 H0Z" fill="var(--navy)"/></svg>
      <svg class="icon" width="90" height="90" viewBox="0 0 90 90" fill="#fff"><rect x="36" y="36" width="18" height="18" transform="rotate(45 45 45)"/><rect x="16" y="8" width="14" height="30" transform="rotate(45 23 23)"/><rect x="60" y="52" width="14" height="30" transform="rotate(45 67 67)"/><path d="M14 62a14 14 0 0 0 14 14M8 62a20 20 0 0 0 20 20" fill="none" stroke="#fff" stroke-width="4"/></svg>
      <h3>Satellite Installation</h3>
      <p>Sed ut perspiciatis unde omnis iste natus error sit voluptatem santium doloremque laudantium</p>
    </article>
    <article class="service-card">
      <div class="top"></div>
      <svg class="wave" viewBox="0 0 235 50" preserveAspectRatio="none"><path d="M0 30 Q60 0 118 22 T235 10 V50 H0Z" fill="#fff"/><path d="M0 36 Q60 8 118 28 T235 16 V50 H0Z" fill="var(--navy)"/></svg>
      <svg class="icon" width="90" height="90" viewBox="0 0 90 90" fill="none" stroke="#fff" stroke-width="4"><circle cx="45" cy="50" r="30"/><path d="M30 52 L45 38 L60 52 V66 H30Z" fill="#fff"/><path d="M60 14a16 16 0 0 1 14 12M62 6a24 24 0 0 1 20 18"/></svg>
      <h3>Smart Home Systems</h3>
      <p>Sed ut perspiciatis unde omnis iste natus error sit voluptatem santium doloremque laudantium</p>
    </article>
    <article class="service-card">
      <div class="top"></div>
      <svg class="wave" viewBox="0 0 235 50" preserveAspectRatio="none"><path d="M0 30 Q60 0 118 22 T235 10 V50 H0Z" fill="#fff"/><path d="M0 36 Q60 8 118 28 T235 16 V50 H0Z" fill="var(--navy)"/></svg>
      <svg class="icon" width="90" height="90" viewBox="0 0 90 90" fill="none" stroke="#fff" stroke-width="7" stroke-linecap="round"><path d="M8 36a52 52 0 0 1 74 0"/><path d="M20 50a34 34 0 0 1 50 0"/><path d="M32 63a16 16 0 0 1 26 0"/><circle cx="45" cy="76" r="4" fill="#fff"/></svg>
      <h3>Wi-Fi System Services</h3>
      <p>Sed ut perspiciatis unde omnis iste natus error sit voluptatem santium doloremque laudantium</p>
    </article>
  </div>
</section>

<section class="how">
  <div class="bg" role="img" aria-label="Dusky city skyline at night seen from above"></div>
  <h2 class="section-title">How It Works</h2>
  <p class="intro">Sed ut perspiciatis unde omnis iste natus error sit voluptatem accusantium doloremque laudantium, totam rem aperiam, eaque ipsa quae ab illo inventore veritatis et quasi architecto beatae vitae dicta sunt explicabo. Nemo enim ipsam voluptatem quia voluptas sit aspernatur aut odit aut fugit, sed quia consequuntur magni dolores eos qui ratione voluptatem sequi nesciunt. Neque porro quisquam</p>
  <div class="steps">
    <svg class="track" width="804" height="4"><line x1="0" y1="2" x2="804" y2="2" stroke="#fff" stroke-width="1.5" stroke-dasharray="4 4"/></svg>
    <div class="step" style="left:217px">
      <div class="circle"><svg width="44" height="44" viewBox="0 0 44 44" fill="none" stroke="#fff" stroke-width="4" stroke-linecap="round"><line x1="8" y1="36" x2="30" y2="14"/><circle cx="33" cy="11" r="6"/><line x1="8" y1="8" x2="36" y2="36"/></svg></div>
      <h4>Browse Our Services</h4>
    </div>
    <div class="step" style="left:494px">
      <div class="circle"><svg width="44" height="44" viewBox="0 0 44 44" fill="none" stroke="#fff" stroke-width="3.5"><rect x="6" y="10" width="26" height="28" rx="3"/><path d="M18 28 L36 8 L40 12 L22 32 L16 34Z"/></svg></div>
      <h4>Get a Quote or Buy</h4>
    </div>
    <div class="step" style="left:754px">
      <div class="circle"><svg width="40" height="44" viewBox="0 0 40 44" fill="#fff"><path d="M20 2a14 14 0 0 1 14 14c0 10-14 26-14 26S6 26 6 16A14 14 0 0 1 20 2zm0 8a6 6 0 1 0 0 12 6 6 0 0 0 0-12z"/></svg></div>
      <h4>Book a Visit</h4>
    </div>
    <div class="step" style="left:1021px">
      <div class="circle"><svg width="44" height="44" viewBox="0 0 44 44" fill="none" stroke="#fff" stroke-width="3.5" stroke-linejoin="round"><rect x="5" y="20" width="8" height="18"/><path d="M13 22 L22 6 c4 0 5 3 4 7 l-2 6 h12 c3 0 4 3 3 5 l-4 12 c-1 2-2 2-4 2 H13"/></svg></div>
      <h4>Job Done</h4>
    </div>
  </div>
</section>

<section class="repair">
  <h2 class="section-title">Need a Repair?</h2>
  <div class="repair-cards">
    <article class="repair-card info" style="left:0;width:311px" role="img" aria-label="Faded photo of a technician at work behind the card text">
      <div class="veil"></div>
      <h3>Trust &amp; Reliability</h3>
      <p>Sed ut perspiciatis unde omnis iste natus error sit voluptatem accusantium doloremque laudantium, totam rem aperiam</p>
      <span class="btn-navy">Read More</span>
    </article>
    <article class="repair-card quick" style="left:346px;width:318px">
      <h3>Quick Find Services</h3>
      <p>Sed ut perspiciatis unde omnis iste natus</p>
      <div class="field">Enter email</div>
      <span class="btn-navy">Sign Up</span>
    </article>
    <article class="repair-card info" style="left:688px;width:322px" role="img" aria-label="Faded photo of rooftops with aerials behind the card text">
      <div class="veil"></div>
      <h3>Our Coverage</h3>
      <p>Sed ut perspiciatis unde omnis iste natus error sit voluptatem accusantium doloremque laudantium, totam rem aperiam</p>
      <span class="btn-navy">Read More</span>
    </article>
  </div>
</section>

<section class="news">
  <h2 class="section-title">Latest News</h2>
  <div class="news-list">
    <article class="news-item">
      <div class="thumb" role="img" aria-label="Couple relaxing on a sofa watching a wall-mounted television" style="background:linear-gradient(135deg,#e9e6df,#c9c2b4 60%,#8f8676)"></div>
      <div class="date">APR 01<br>2018</div>
      <h3>Nemo enim ipsam volupta</h3>
      <p>Sed ut perspiciatis unde omnis iste natus error sit voluptatem accusantium</p>
    </article>
    <article class="news-item">
      <div class="thumb" role="img" aria-label="Family gathered around a tablet at home" style="background:linear-gradient(135deg,#b5c6d6,#6e8aa6 55%,#3b4f66)"></div>
      <div class="date">APR 01<br>2018</div>
      <h3>Nemo enim ipsam volupta</h3>
      <p>Sed ut perspiciatis unde omnis iste natus error sit voluptatem accusantium</p>
    </article>
    <article class="news-item">
      <div class="thumb" role="img" aria-label="Hand holding a smartphone showing a wireless signal" style="background:linear-gradient(135deg,#9fb3cc,#4e6a8e 55%,#2a3c58)"></div>
      <div class="date">APR 01<br>2018</div>
      <h3>Nemo enim ipsam volupta</h3>
      <p>Sed ut perspiciatis unde omnis iste natus error sit voluptatem accusantium</p>
    </article>
  </div>
</section>

<section class="testimonial">
  <span class="corner tl"></span><span class="corner br"></span>
  <div class="quote-mark">&rdquo;</div>
  <blockquote>Sed ut perspiciatis unde omnis iste natus error sit voluptatem accusantium doloremque laudantium, totam rem aperiam, eaque ipsa quae ab illo inventore veritatis et quasi architecto beatae vitae dicta sunt explicabo. Nemo enim ipsam voluptatem quia voluptas sit aspernatur aut odit aut fugit, sed quia consequuntur .</blockquote>
  <cite>Ravi Tenholt - Corvid Mend &amp; Reach</cite>
  <div class="slider-bar"><span class="on"></span><span></span></div>
</section>

<section class="partners">
  <span>Veloxa</span><span>Ambrin</span><span>Stanwick</span><span>Lumora</span><span>Fernly</span><span>Haldor</span>
</section>

<footer class="site-footer">
  <div class="footer-col quick-links">
    <h4>Quick Link</h4>
    <ul><li>Home</li><li>What We Do</li><li>Services</li><li>Solutions</li><li>Blog</li><li>Contact Us</li></ul>
  </div>
  <div class="footer-col contact">
    <h4>Contact Us</h4>
    <div class="row"><svg width="12" height="14" viewBox="0 0 40 44" fill="#ccc"><path d="M20 2a14 14 0 0 1 14 14c0 10-14 26-14 26S6 26 6 16A14 14 0 0 1 20 2zm0 8a6 6 0 1 0 0 12 6 6 0 0 0 0-12z"/></svg><span>Corvid Mend &amp; Reach<br>48 Larkspur Row, Suite 12 Fenmoor,<br>Westvale 40917, United States</span></div>
    <div class="row"><svg width="12" height="12" viewBox="0 0 24 24" fill="#ccc"><path d="M6.6 10.8a15 15 0 0 0 6.6 6.6l2.2-2.2c.3-.3.7-.4 1-.2 1.1.4 2.3.6 3.6.6.6 0 1 .4 1 1V20c0 .6-.4 1-1 1A17 17 0 0 1 3 4c0-.6.4-1 1-1h3.5c.6 0 1 .4 1 1 0 1.3.2 2.5.6 3.6.1.3 0 .7-.2 1z"/></svg><span>Phone : 555-016-4471, 555-016-4472</span></div>
    <div class="row"><svg width="13" height="11" viewBox="0 0 24 20" fill="#ccc"><path d="M2 0h20a2 2 0 0 1 2 2v16a2 2 0 0 1-2 2H2a2 2 0 0 1-2-2V2a2 2 0 0 1 2-2zm10 9 10-6V2L12 8 2 2v1z"/></svg><span>Email : hello@corvidmendreach.example</span></div>
  </div>
  <div class="footer-col quote">
    <h4>Get a Quote</h4>
    <p>Lorem ipsum dolor sit amet, consectetur adipisicing elit, sed do eiusmod tempor incididunt ut labore et dolore magna aliqua. Ut enim ad minim veniam.</p>
    <div class="grid">
      <div class="input">Name</div><div class="input">E - Mail</div>
      <div class="input">Phone No</div><div class="submit">Submit Now!</div>
    </div>
  </div>
  <div class="footer-bottom">
    <div class="socials"><span></span><span></span><span></span><span></span></div>
    <p class="copyright">© 2018 Corvid Mend &amp; Reach. All Rights Reserved.</p>
  </div>
</footer>

</body>
</html>
```